Book Cover - Life Lessons Book

I have written a book for my sons who are graduating high school and college. Working title is "Keep The Lantern Lit.....52 Porch Stories for Kin" I am looking for the book to appeal to young adults and parents who would want to give this book to them. It is a 125 page book that will be hardback and paperback - probably 5x8 or 6x9.
Updates

Reason: Altered some of the design elements based on the first submissions received. Would really like to have designs by Monday, May 15, 2016 but could not force a 2 day extension.

Target Market(s)

Young adults -- graduates, 20-3- year olds. And, parents would would give a book to their kids

Industry/Entity Type

Book Publisher

Font styles to use
Serif

Requirements
Must have
• Great design. It is a book cover so needs to catch the attention.
Nice to have
• I am open to more animated/playful/modern look or a more traditional look. Just would like to appeal to young adults and parents.
Should not have
• Anything in poor taste

```html
<!DOCTYPE html>
<html lang="en">
<head>
<meta charset="utf-8">
<title>Keep The Lantern Lit — Book Cover</title>
<link href="https://fonts.googleapis.com/css2?family=Marcellus&family=Oswald:wght@700&display=swap" rel="stylesheet">
<style>
  :root {
    --page-bg: #dfe2e6;
    --sky-top: #46475a;
    --sky-mid: #6d6580;
    --sky-rose: #c6a2a9;
    --sky-glow: #efc7a9;
    --horizon: #f1cf6e;
    --cloud: #cdcdd4;
    --ground: #2a292d;
    --ground-deep: #141416;
    --title-light: #ececf0;
    --title-blue: #3c4a8d;
  }
  html, body {
    margin: 0;
    padding: 0;
    width: 960px;
    height: 1200px;
    overflow: hidden;
    background: var(--page-bg);
  }
  .cover {
    position: relative;
    width: 960px;
    height: 1200px;
    overflow: hidden;
  }
  .cover-photo {
    position: absolute;
    inset: 0;
    background: linear-gradient(
      to bottom,
      var(--sky-top) 0%,
      var(--sky-mid) 28%,
      var(--sky-rose) 52%,
      var(--sky-glow) 66%,
      var(--horizon) 73%,
      var(--cloud) 77%,
      var(--cloud) 81%,
      var(--ground) 86%,
      var(--ground-deep) 100%
    );
  }
  .title {
    position: absolute;
    margin: 0;
    line-height: 1;
    white-space: nowrap;
    font-family: "Marcellus", serif;
    font-weight: 400;
  }
  .title--light { color: var(--title-light); }
  .title--blue { color: var(--title-blue); }
  .title-keep { top: 78px; left: 158px; font-size: 150px; }
  .title-keep .title-small { font-size: 64px; margin-left: 6px; }
  .title-lantern { top: 245px; left: 162px; font-size: 128px; }
  .number {
    position: absolute;
    top: 330px;
    left: 196px;
    margin: 0;
    font-family: "Oswald", sans-serif;
    font-weight: 700;
    font-size: 300px;
    line-height: 1;
    letter-spacing: -6px;
    color: var(--title-blue);
  }
  .title-porch { top: 405px; left: 536px; font-size: 122px; }
  .title-stories { top: 528px; left: 544px; font-size: 60px; }
  .title-for { top: 618px; left: 196px; font-size: 120px; }
  .title-kin { top: 618px; left: 536px; font-size: 122px; }
</style>
</head>
<body>
  <main class="cover">
    <div class="cover-photo" role="img" aria-label="Photograph of a hiker with a backpack seen from behind, standing on a dark mountaintop above a sea of clouds at sunset, under a purple-to-pink sky with a golden horizon"></div>

    <h1 class="title title--light title-keep">Keep<span class="title-small">The</span></h1>
    <p class="title title--light title-lantern">Lantern Lit</p>

    <p class="number">52</p>
    <p class="title title--blue title-porch">Porch</p>
    <p class="title title--blue title-stories">Stories</p>
    <p class="title title--blue title-for">For</p>
    <p class="title title--blue title-kin">Kin</p>
  </main>
</body>
</html>
```